kolvarin.link kolvarin.space kolvarin.press website

The website is named KOLVARIN and it will have 3 domain names. kolvarin.link, press, space.
I'd like it to be viewed on Pads, pcs and phones.

page menu:

kolvarin.link(start page): presentation of company. (creative, design, app, new product innovation.)
Here we'll need sosial media icons: plimber, vendoloop, mirtavel, trelvanet. (light but some 'fruity' colors)

kolvarin.press: blog. It will be a 75% picture blog > rest will be text. I need to be able to resize pictures and shape columns to picture size. (light but some 'fruity' colors)

kolvarin.space : the fun part of this web design, however, on entering the page I'd like a non-disclosure agreement where viewer simply click "yes, I agree" after filling out contact info. (check attached document)
We will have space here for uploading PDF files viewers can download. There is also a blog space here to tell in brief about the PDF file. (maybe a space/sci-fi theme her e.g spacechimp, Laika the space dog?)

I will attach the logo here I want you to use > and develop for the .space .press webpage. The logo i uploaded is for the .link page.

Target Market(s)

venture capitalists

Number of Pages Required

3 page

Requirements
Must have
• a few 'fruity colors' but mostly white and grey

```html
<!DOCTYPE html>
<html lang="en">
<head>
<meta charset="utf-8">
<title>Kolvarin Link</title>
<link href="https://fonts.googleapis.com/css2?family=Arimo:wght@400;700&family=Comfortaa:wght@500;700&display=swap" rel="stylesheet">
<style>
:root{
  --green:#4f8f3a;
  --green-dark:#2f6a2a;
  --red:#e24a2f;
  --title-red:#d93a22;
  --pink:#f9dcdc;
  --text:#333;
  --grey-line:#e3e3e3;
  --white:#fff;
}
*{margin:0;padding:0;box-sizing:border-box}
html,body{width:942px;height:1200px;overflow:hidden;background:var(--white)}
body{font-family:"Arimo",Arial,sans-serif;color:var(--text);position:relative}
.topbar{position:absolute;left:0;top:0;width:942px;height:28px}
.topbar-band{position:absolute;left:0;top:0}
.contact{position:absolute;top:7px;font-size:11.5px;color:#666;white-space:nowrap}
.contact.email{left:530px}
.contact.phone{left:666px;top:4px;display:flex;align-items:center;gap:4px}
.phone-icon{display:block;flex:none}
.divider{position:absolute;top:0;width:1px;height:28px;background:#fff}
.social{position:absolute;left:784px;top:6px;display:flex;gap:3px}
.social span{font-size:7px;color:var(--white);background:var(--red);padding:2px 2px;line-height:12px}
.brand{position:absolute;left:70px;top:18px;display:flex;align-items:center;gap:5px;font-weight:700;font-size:19px;color:#111;letter-spacing:.5px}
.brand i{display:block;width:12px;height:12px;background:var(--red)}
.nav{position:absolute;left:494px;top:28px;display:flex;height:34px;font-size:12px}
.nav a{color:#333;text-decoration:none;line-height:34px;padding:0 16px;position:relative}
.nav a.active{background:var(--green);color:var(--white);width:72px;text-align:center;padding:0}
.nav a+a:not(:nth-child(2))::before{content:"";position:absolute;left:0;top:13px;height:9px;width:1px;background:#ccc}
.hero{position:absolute;left:0;top:62px;width:942px;height:436px}
.hero-photo{position:absolute;inset:0;background:linear-gradient(180deg,#3f78b6 0%,#8fb7dc 45%,#d7d9cf 70%,#caa46a 82%,#3a3a3a 100%)}
.hero-cut{position:absolute;left:0;top:0}
.caption{position:absolute;left:0;bottom:0;width:100%;height:38px;background:rgba(30,30,30,.72);color:var(--white);font-size:17px;text-align:center;line-height:38px}
.arrow{position:absolute;top:184px;width:31px;height:26px;background:#333;border:1px solid #888}
.arrow.prev{left:0}.arrow.next{right:0}
.arrow svg{display:block;margin:6px auto}
.section-title{position:absolute;left:0;width:942px;text-align:center;font-family:"Comfortaa",sans-serif;font-weight:700;font-size:25px;color:var(--green-dark)}
.section-title em{font-style:normal;color:var(--title-red)}
.rule{position:absolute;left:316px;width:320px;height:2px;background:var(--grey-line)}
.rule::after{content:"";position:absolute;left:133px;top:-1px;width:54px;height:3px;background:var(--green)}
.service{position:absolute;top:603px;width:204px;height:215px;text-align:center}
.service.featured{color:var(--white)}
.service .card{position:absolute;inset:0}
.service .badge{position:absolute;left:55px;top:15px}
.service h3{position:absolute;top:120px;width:100%;font-weight:400;font-size:15px}
.service p{position:absolute;top:148px;left:8px;right:8px;font-size:12px;line-height:18px}
.welcome p{position:absolute;left:75px;width:800px;text-align:center;font-size:11.8px;line-height:17.6px}
.read-more{position:absolute;left:0;width:942px;top:1071px;text-align:center;font-size:11px;font-weight:700}
.read-more a{color:#111}
.footer{position:absolute;left:0;top:1128px}
.copyright{position:absolute;left:69px;top:1173px;font-size:9px;color:var(--white)}
.footer-brand{position:absolute;left:772px;top:1150px;font-weight:700;font-size:16px;color:#222;display:flex;align-items:center;gap:4px}
.footer-brand i{display:block;width:10px;height:10px;background:#222}
</style>
</head>
<body>

<header class="topbar">
  <svg class="topbar-band" width="942" height="28"><polygon points="257,28 285,0 942,0 942,28" fill="var(--pink)"/></svg>
  <span class="contact email">sales@velmora.com.au</span>
  <span class="divider" style="left:654px"></span>
  <span class="contact phone">
    <svg class="phone-icon" width="18" height="18" viewBox="0 0 18 18"><circle cx="9" cy="9" r="8" fill="none" stroke="var(--red)" stroke-width="1.3"/><path d="M6.5 5 l2 2-1 1.2c.6 1.3 1.4 2.1 2.6 2.6l1.2-1 2 2-1.2 1.3C8.6 12.6 5.6 9.6 5.3 6.2z" fill="var(--red)"/></svg>
    (123) 555 0142
  </span>
  <span class="divider" style="left:778px"></span>
  <nav class="social" aria-label="Social media">
    <span>mirtavel</span><span>plimber</span><span>orvanta</span><span>trelvanet</span>
  </nav>
</header>

<div class="hero">
  <div class="hero-photo" role="img" aria-label="Business team silhouettes at sunrise in front of hand-drawn teamwork and technology sketches"></div>
  <svg class="hero-cut" width="260" height="14"><polygon points="0,0 260,0 215,14 0,14" fill="var(--white)"/></svg>
  <div class="arrow prev"><svg width="10" height="12"><path d="M7 1 2 6l5 5" stroke="#fff" stroke-width="2.4" fill="none"/></svg></div>
  <div class="arrow next"><svg width="10" height="12"><path d="M3 1l5 5-5 5" stroke="#fff" stroke-width="2.4" fill="none"/></svg></div>
  <div class="caption">Lorem Ipsum Dolor Sit Amet Consectetuer Adipiscing Elit Sed Diam Nonummy Nibh</div>
</div>

<div class="brand"><i></i>KOLVARIN</div>

<nav class="nav">
  <a class="active" href="#">Home</a><a href="#">About</a><a href="#">Services</a><a href="#">Our Work</a><a href="#">Contact</a>
</nav>

<h2 class="section-title" style="top:524px">Our <em>Services</em></h2>
<div class="rule" style="top:558px"></div>

<section class="service" style="left:58px">
  <svg class="badge" width="94" height="94"><circle cx="47" cy="47" r="45" fill="none" stroke="var(--green)" stroke-width="3"/><circle cx="47" cy="47" r="39" fill="var(--green)"/><circle cx="47" cy="40" r="7" fill="#fff"/><rect x="44" y="47" width="6" height="4" fill="#fff"/><path d="M33 62c2-8 7-9 14-9s12 1 14 9z" fill="#fff"/></svg>
  <h3>Creative</h3>
  <p>Lorem ipsum dolor sit amet, consectetuer adipiscing elit, sed diam nonummy nibh.</p>
</section>

<section class="service featured" style="left:266px">
  <svg class="card" width="204" height="215"><polygon points="0,0 170,0 204,34 204,215 34,215 0,181" fill="var(--green)"/></svg>
  <svg class="badge" width="94" height="94"><circle cx="47" cy="47" r="45" fill="none" stroke="var(--green-dark)" stroke-width="3"/><circle cx="47" cy="47" r="39" fill="var(--green-dark)"/><rect x="37" y="32" width="17" height="24" rx="2" fill="none" stroke="#fff" stroke-width="2"/><rect x="50" y="44" width="9" height="15" rx="1.5" fill="#fff"/><circle cx="45" cy="42" r="3" fill="#fff"/></svg>
  <h3>App Development</h3>
  <p>Lorem ipsum dolor sit amet, consectetuer adipiscing elit, sed diam nonummy nibh.</p>
</section>

<section class="service" style="left:484px">
  <svg class="badge" width="94" height="94"><circle cx="47" cy="47" r="45" fill="none" stroke="var(--green)" stroke-width="3"/><circle cx="47" cy="47" r="39" fill="var(--green)"/><circle cx="37" cy="36" r="5" fill="none" stroke="#fff" stroke-width="2.5"/><circle cx="48" cy="31" r="4" fill="none" stroke="#fff" stroke-width="2"/><path d="M44 40c9 0 14 6 13 13l3 5h-4v6h-8v5H38V58c-3-4-3-10 1-14z" fill="#fff"/></svg>
  <h3>New Product Innovations</h3>
  <p>Lorem ipsum dolor sit amet, consectetuer adipiscing elit, sed diam nonummy nibh.</p>
</section>

<section class="service" style="left:692px">
  <svg class="badge" width="94" height="94"><circle cx="47" cy="47" r="45" fill="none" stroke="var(--green)" stroke-width="3"/><circle cx="47" cy="47" r="39" fill="var(--green)"/><rect x="29" y="32" width="36" height="25" rx="2" fill="none" stroke="#fff" stroke-width="2.5"/><rect x="44" y="57" width="6" height="5" fill="#fff"/><rect x="38" y="62" width="18" height="2.5" fill="#fff"/><path d="M38 51l3-6 12-12 3 3-12 12z" fill="#fff"/></svg>
  <h3>Design</h3>
  <p>Lorem ipsum dolor sit amet, consectetuer adipiscing elit, sed diam nonummy nibh.</p>
</section>

<h2 class="section-title" style="top:900px">Welcome to <em>Kolvarin Link</em></h2>
<div class="rule" style="top:941px"></div>

<div class="welcome">
  <p style="top:960px">Lorem ipsum dolor sit amet, consectetuer adipiscing elit, sed diam nonummy nibh euismod tincidunt ut laoreet dolore magna aliquam erat volutpat. Ut wisi enim ad minim veniam, quis nostrud exerci tation ullamcorper suscipit lobortis nisl ut aliquip ex ea commodo consequat. Duis autem vel eum iriure dolor in hendrerit in vulputate velit esse molestie consequat, vel illum dolore eu feugiat nulla facilisis at vero eros et accumsan et iusto odio dignissim qui blandit praesent luptatum zzril delenit augue duis dolore te feugait nulla facilisi.</p>
  <p style="top:1037px">We are committed to providing our customers with quality products, designs and 100% Work Satisfaction</p>
</div>
<div class="read-more"><a href="#">Read More</a></div>

<footer>
  <svg class="footer" width="942" height="72"><polygon points="0,25 712,25 732,2 942,2 942,72 0,72" fill="var(--green)"/><polygon points="0,29 714,29 734,6 942,6 942,72 0,72" fill="var(--red)"/></svg>
  <div class="footer-brand"><i></i>KOLVARIN</div>
  <p class="copyright">Copyright© 2016 &nbsp;Kolvarin Link &nbsp;All rights reserved</p>
</footer>

</body>
</html>
```